Natural Light/Organic/Documentary Photography Business

I like a simple, approachable, feminine, earthy/organic feel. Earth/neutral tones, nothing too loud or obnoxious. I like the watercolor look. I don't want anything too trendy or something I'll get tired of after a couple months. As far as colors, I am much more a fan of cream/taupe/blue/green...not a fan of pink or purple at all.

Target Market(s)

Weddings & Families

Industry/Entity Type

Wedding Photography

Contact Information for Business Card

website, email, phone number

Font styles to use
Other font styles liked:
• Horizontes, Gotham

Colors

Designer to choose colors to be used in the design.

Requirements
Must have
• Website: www.mirelhatchway.com
• Phone: 418.629.5073
• Email: mirel@mirelhatchway.com
Nice to have
• I like the watercolor look but its not necessary. I like simple/earthy tones. Nothing too loud or distracting. Simple & feminine without being too girly. I like an approachable/soft feel.
• Instagram: www.instagram.com/mirelhatchwayphotography/
Should not have
• NO loud colors or design or pattern. I do not want a photo of a camera or lens or anything cheesy like that.

```html
<!DOCTYPE html>
<html lang="en">
<head>
<meta charset="utf-8">
<title>Mirel Hatchway Photography – Business Card</title>
<link rel="stylesheet" href="https://fonts.googleapis.com/css2?family=Source+Sans+3:wght@400;600&display=swap">
<style>
  :root {
    --backdrop: #ececec;
    --card: #ffffff;
    --taupe: #8c7f76;
    --ink: #4a4646;
    --band-text: #ffffff;
  }
  * { margin: 0; padding: 0; box-sizing: border-box; }
  html, body {
    width: 1200px;
    height: 799px;
    overflow: hidden;
    background: var(--backdrop);
    font-family: "Source Sans 3", sans-serif;
  }
  .canvas {
    position: relative;
    width: 1200px;
    height: 799px;
  }
  .card {
    position: absolute;
    left: 313px;
    width: 584px;
    height: 334px;
    background: var(--card);
  }
  .card--front { top: 51px; }
  .card--back  { top: 413px; }

  /* Front */
  .monogram-mark {
    position: absolute;
    left: 50%;
    top: 80px;
    width: 64px;
    height: 64px;
    margin-left: -32px;
    border: 1.5px solid var(--taupe);
    border-radius: 50%;
  }
  .front-name {
    position: absolute;
    top: 186px;
    width: 100%;
    text-align: center;
    font-size: 20px;
    font-weight: 600;
    color: var(--taupe);
  }
  .contact-row {
    position: absolute;
    width: 100%;
    display: flex;
    justify-content: center;
    align-items: center;
    gap: 4px;
    font-size: 14px;
    color: var(--ink);
    white-space: nowrap;
  }
  .contact-row--one { top: 221px; }
  .contact-row--two { top: 240px; }
  .contact-item { display: inline-flex; align-items: center; gap: 3px; }
  .contact-icon { width: 12px; height: 12px; fill: var(--ink); }
  .social-square {
    display: inline-block;
    width: 11px;
    height: 11px;
    background: var(--ink);
    border-radius: 2px;
  }

  /* Back */
  .brand-name {
    position: absolute;
    top: 128px;
    width: 100%;
    text-align: center;
    font-size: 34px;
    font-weight: 400;
    color: var(--taupe);
    letter-spacing: 1px;
  }
  .brand-tagline {
    position: absolute;
    top: 172px;
    width: 100%;
    text-align: center;
    font-size: 9px;
    font-weight: 400;
    letter-spacing: 4px;
    color: var(--taupe);
  }
  .web-band {
    position: absolute;
    top: 277px;
    left: 0;
    width: 100%;
    height: 24px;
    background: var(--taupe);
    color: var(--band-text);
    font-size: 15px;
    font-weight: 600;
    letter-spacing: 4.5px;
    text-align: center;
    line-height: 24px;
  }
</style>
</head>
<body>
<div class="canvas">

  <section class="card card--front">
    <div class="monogram-mark"></div>
    <h1 class="front-name">Mirel Hatchway</h1>

    <p class="contact-row contact-row--one">
      <span class="contact-item">
        <svg class="contact-icon" viewBox="0 0 24 24" aria-hidden="true"><path d="M6.6 10.8c1.4 2.8 3.8 5.1 6.6 6.6l2.2-2.2c.3-.3.7-.4 1-.2 1.1.4 2.3.6 3.6.6.6 0 1 .4 1 1V20c0 .6-.4 1-1 1C10.6 21 3 13.4 3 4c0-.6.4-1 1-1h3.5c.6 0 1 .4 1 1 0 1.3.2 2.5.6 3.6.1.3 0 .7-.2 1L6.6 10.8z"/></svg>
        418.629.5073
      </span>
      <span class="contact-item">
        <svg class="contact-icon" viewBox="0 0 24 24" aria-hidden="true"><path d="M2 5h20v14H2z M2 5l10 7 10-7" fill="var(--ink)"/><path d="M3 6l9 6.3L21 6" stroke="#fff" stroke-width="1.5" fill="none"/></svg>
        mirel@mirelhatchway.com
      </span>
    </p>

    <p class="contact-row contact-row--two">
      <span class="contact-item">
        <svg class="contact-icon" viewBox="0 0 24 24" aria-hidden="true"><circle cx="12" cy="12" r="10"/><path d="M2 12h20M12 2c3 3 3 17 0 20M12 2c-3 3-3 17 0 20" stroke="#fff" stroke-width="1.4" fill="none"/></svg>
        www.mirelhatchway.com
      </span>
      <span class="contact-item">
        <span class="social-square"></span>
        mirelhatchwayphotography
      </span>
    </p>
  </section>

  <section class="card card--back">
    <h2 class="brand-name">Mirel Hatchway</h2>
    <p class="brand-tagline">PHOTOGRAPHY</p>
    <div class="web-band">WWW.MIRELHATCHWAY.COM</div>
  </section>

</div>
</body>
</html>
```